Road Construction Company needs business cards

We would like a new business card designed for our business.

We're a road construction company based in Qld, Australia.

Can the business card please have the following information on it.

Name: Warren Halbeck
Position: General Manager
Phone: 0472 915 348
Email: Warren.halbeck@tovrin.com.au
Address: 87 Marrow Ave, Pendlebay, QLD, 4023
Website: www.tovrin.com.au

Visually we'd like the card to be professional and simple.

Attached is our logo.

Our website is www.tovrin.com.au

Target Market(s)

Men aged 25-60

Contact Information for Business Card

As listed in project description

Font styles to use
Serif

Requirements
Must have
• Large logo on back of card

```html
<!DOCTYPE html>
<html lang="en">
<head>
<meta charset="utf-8">
<title>Tovrin Business Cards</title>
<link href="https://fonts.googleapis.com/css2?family=Saira:wght@400;500;800&display=swap" rel="stylesheet">
<style>
  :root {
    --bg: #1d1d1f;
    --royal: #0553a3;
    --sky: #35a6d9;
    --white: #ffffff;
    --card-w: 700px;
    --card-h: 400px;
  }
  * { margin: 0; padding: 0; box-sizing: border-box; }
  html, body { width: 1200px; height: 1015px; overflow: hidden; }
  body {
    background: var(--bg);
    font-family: "Saira", sans-serif;
    position: relative;
  }
  .card {
    position: absolute;
    left: 250px;
    width: var(--card-w);
    height: var(--card-h);
    overflow: hidden;
    box-shadow: 0 14px 30px rgba(0,0,0,.55);
  }
  .card--front { top: 70px; background: var(--royal); }
  .card--back { top: 545px; background: var(--white); }

  .band {
    position: absolute;
    left: 0; right: 0;
    background: var(--sky);
    display: flex;
    align-items: center;
  }
  .card--front .band { top: 262px; height: 42px; justify-content: center; }
  .card--back .band { top: 262px; height: 42px; }

  .website {
    color: var(--white);
    font-size: 19px;
    letter-spacing: 3px;
    font-weight: 400;
  }

  .brand {
    display: flex;
    align-items: center;
    gap: 14px;
    font-weight: 800;
    letter-spacing: 2px;
    text-transform: uppercase;
  }
  .brand__mark { width: 22px; height: 22px; }
  .card--front .brand {
    position: absolute;
    top: 118px; left: 0; right: 0;
    justify-content: center;
    color: var(--white);
    font-size: 64px;
  }
  .card--front .brand__mark { background: var(--sky); }

  .back__panel {
    position: absolute;
    top: 0; bottom: 0;
    left: 300px; right: 0;
    background: var(--royal);
  }
  .card--back .brand {
    position: absolute;
    top: 140px; left: 36px;
    color: var(--royal);
    font-size: 46px;
  }
  .card--back .brand__mark { background: var(--sky); width: 18px; height: 18px; }
  .card--back .website {
    position: absolute;
    left: 370px;
    font-size: 17px;
  }

  .contact {
    position: absolute;
    top: 48px; left: 340px;
    color: var(--white);
  }
  .contact__name {
    color: var(--sky);
    font-weight: 800;
    font-size: 24px;
    letter-spacing: 2px;
    text-transform: uppercase;
    line-height: 1.1;
  }
  .contact__role { font-size: 17px; font-weight: 500; margin-bottom: 16px; }
  .contact__line {
    display: flex; align-items: center; gap: 10px;
    font-size: 16px; line-height: 1.5;
  }
  .contact__line svg { width: 16px; height: 16px; flex: none; }
  .contact__address { margin-top: 14px; padding-left: 26px; font-size: 16px; line-height: 1.4; }
</style>
</head>
<body>

<section class="card card--front" aria-label="Card front">
  <div class="brand"><span class="brand__mark"></span>Tovrin</div>
  <div class="band"><span class="website">www.tovrin.com.au</span></div>
</section>

<section class="card card--back" aria-label="Card back">
  <div class="back__panel"></div>
  <div class="brand"><span class="brand__mark"></span>Tovrin</div>
  <div class="contact">
    <p class="contact__name">Warren Halbeck</p>
    <p class="contact__role">General Manager</p>
    <p class="contact__line">
      <svg viewBox="0 0 16 16" fill="none" stroke="#35a6d9" stroke-width="1.6"><path d="M4 2l2 3-1.5 1.5a8 8 0 0 0 5 5L11 10l3 2-1 2.5C7 14 2 9 1.5 3z"/></svg>
      0472 915 348
    </p>
    <p class="contact__line">
      <svg viewBox="0 0 16 16" fill="#35a6d9"><path d="M1 3h14v10H1z"/><path d="M1 3l7 6 7-6" fill="none" stroke="#0553a3" stroke-width="1.4"/></svg>
      Warren.halbeck@tovrin.com.au
    </p>
    <p class="contact__address">87 Marrow Ave<br>Pendlebay, QLD, 4023</p>
  </div>
  <div class="band"><span class="website">www.tovrin.com.au</span></div>
</section>

</body>
</html>
```